Hearthline Insurance Provider Website

We are selling Hearthline Insurance policy / tenants Policy/Flood Insurance in USA in few states and planning expand nationally.

Our target audience are two folds: Customers (Buy policies) and Insurance Agents who wants to work with us to sell our policies to customers. But website should focus 80% on customers and 20% on agents. So, more customer focused user experience. Please note that there is no direct buy option for customers. They always go through insurance agents.

Customer focused, educational that makes buyer journey easy. We don’t want to come off as trying sell something as there is no direct sales involved from website.

Target Market(s)

Homeowners in USA and Insurance agent who sells these insurance.

Industry/Entity Type

Insurance

Number of Pages Required

4 page

Font styles to use
Other font styles liked:
• Open to suggestions

Colors

Designer to choose colors to be used in the design.

Requirements
Must have
• Three most important things: Trustworthy, Authentic, Simple
• Please use colors form logo and grays
• We like: www.hollowmere.com
• https://www.quillfenbrook.com/
• We need Agent Look up tool on home page similar to what is shown on example sites.
• Design:
• Home Page - Open to Ideas
• Insurance (Products) Landing Page - Info similar to: https://www.quillfenbrook.com/insurance/
• Agents Page - https://www.quillfenbrook.com/agents/
• Claims Page - Information similar to: https://www.quillfenbrook.com/claims-center/
• Site Navigation:
• Home
• Insurance
• Claims
• Agents
• About Us
• Contact Us
Nice to have
• Elegant, minimal and clean design that reflects trust and authenticity.
Should not have
• Slider or rotating images - prefer flat design. Not over powering design.

```html
<!DOCTYPE html>
<html lang="en">
<head>
<meta charset="utf-8">
<title>Hearthline Insurance Co.</title>
<link rel="stylesheet" href="https://fonts.googleapis.com/css2?family=Source+Sans+3:wght@400;600;700&display=swap">
<style>
:root{
  --navy:#1b3f8f;
  --blue:#1a4fa3;
  --blue-dark:#183a80;
  --red:#d7181f;
  --ink:#333;
  --gray:#555;
  --footer:#161616;
  --white:#fff;
}
*{box-sizing:border-box;margin:0;padding:0}
html,body{width:1200px;height:966px;overflow:hidden}
body{font-family:"Source Sans 3","Source Sans Pro",sans-serif;color:var(--ink);background:#f4f4f4;position:relative}
a{text-decoration:none}
.hero{position:absolute;left:0;top:0;width:1200px;height:675px;overflow:hidden}
.hero-photo{position:absolute;inset:0;background:
  radial-gradient(ellipse 260px 330px at 330px 360px,#d8cfc7 0%,rgba(216,207,199,.55) 45%,rgba(240,240,240,0) 100%),
  radial-gradient(ellipse 160px 160px at 60px 420px,rgba(170,190,140,.55),rgba(240,240,240,0) 100%),
  linear-gradient(180deg,#f5f5f5 0%,#efefef 55%,#e9e7e6 100%)}
.header{position:absolute;left:0;top:0;width:1200px;height:70px}
.brand{position:absolute;left:172px;top:17px;display:flex;align-items:center;gap:9px;color:var(--navy);font-weight:700;font-size:17px;line-height:17px;letter-spacing:.5px;white-space:nowrap}
.brand-mark{width:32px;height:32px;border-radius:50%;background:var(--navy);flex:none}
.nav a{position:absolute;top:28px;font-size:14px;font-weight:600;color:var(--gray);white-space:nowrap;line-height:17px}
.nav a.active{color:var(--red)}
.btn{display:flex;align-items:center;justify-content:center;gap:5px;color:var(--white);font-weight:600;border-radius:2px;white-space:nowrap}
.btn-careers{position:absolute;left:850px;top:20px;width:87px;height:33px;background:var(--blue);font-size:14px}
.btn-login{position:absolute;left:941px;top:20px;width:86px;height:33px;background:var(--red);font-size:14px}
.finder{position:absolute;left:560px;top:187px;width:444px;text-align:center}
.finder h1{font-size:28px;font-weight:700;color:#333;line-height:32px}
.finder p{margin-top:12px;font-size:15px;line-height:19px;color:var(--gray)}
.zip{position:absolute;left:635px;top:294px;width:147px;height:40px;background:var(--white);border:1px solid #ddd;font-size:13px;color:#999;padding:11px 13px}
.btn-find{position:absolute;left:790px;top:294px;width:141px;height:40px;background:var(--red);font-size:15px}
.product{position:absolute;top:472px;width:180px;height:180px;border-radius:50%;background:rgba(255,255,255,.85);box-shadow:0 2px 8px rgba(0,0,0,.12)}
.product-inner{position:absolute;left:9px;top:9px;width:162px;height:162px;border-radius:50%;background:linear-gradient(180deg,var(--blue) 0%,var(--blue-dark) 100%);display:flex;flex-direction:column;align-items:center;color:var(--white);font-weight:600;font-size:14.5px;text-align:center;line-height:16px}
.product-inner svg{margin-top:34px;margin-bottom:14px;height:46px}
.footer{position:absolute;left:0;top:675px;width:1200px;height:291px;background:var(--footer);color:var(--white)}
.col{position:absolute;top:42px;white-space:nowrap}
.col h3{font-size:15px;font-weight:600;margin-bottom:12px;line-height:18px}
.col ul{list-style:none;font-size:12px;line-height:19.5px}
.phone{font-size:17px;font-weight:600;line-height:20px}
.email{font-size:12px}
.social{display:flex;gap:6px;margin-top:16px}
.social span{width:30px;height:30px;border:2px solid var(--white);border-radius:50%}
.btn-footer{position:absolute;left:539px;top:126px;width:141px;height:40px;border:2px solid var(--white);font-size:14.5px}
.legal{position:absolute;left:0;top:214px;width:1200px;text-align:center;font-size:12px;line-height:19.5px}
</style>
</head>
<body>
<section class="hero">
  <div class="hero-photo" role="img" aria-label="Smiling woman relaxing on a bed with a laptop and a mug in a bright bedroom"></div>

  <header class="header">
    <div class="brand"><span class="brand-mark"></span><span>HEARTHLINE<br>INSURANCE CO.</span></div>
    <nav class="nav">
      <a class="active" href="#" style="left:443px">Home</a>
      <a href="#" style="left:496px">Insurance</a>
      <a href="#" style="left:570px">About Us</a>
      <a href="#" style="left:641px">Claims</a>
      <a href="#" style="left:697px">Agents</a>
      <a href="#" style="left:755px">Contact Us</a>
    </nav>
    <a class="btn btn-careers"><svg width="11" height="12" viewBox="0 0 11 12"><circle cx="5.5" cy="3" r="3" fill="#fff"/><path d="M0 12c0-4 2.5-5 5.5-5s5.5 1 5.5 5z" fill="#fff"/></svg>Careers</a>
    <a class="btn btn-login"><svg width="9" height="12" viewBox="0 0 9 12"><path d="M2 5V3.5a2.5 2.5 0 0 1 5 0V5" stroke="#fff" stroke-width="1.6" fill="none"/><rect x="0" y="5" width="9" height="7" rx="1" fill="#fff"/></svg>Login</a>
  </header>

  <div class="finder">
    <h1>Find an Agent</h1>
    <p>Talk to one of our local independent agencies to get a quote,<br>ask questions about coverage options &amp; more!</p>
  </div>
  <div class="zip">ZIP Code</div>
  <a class="btn btn-find"><svg width="18" height="18" viewBox="0 0 18 18" fill="none" stroke="#fff" stroke-width="1.6"><circle cx="8" cy="8" r="6.5"/><circle cx="8" cy="6.5" r="2"/><path d="M4.5 11.5c1-2 6-2 7 0M12.7 12.7L17 17"/></svg>Find an Agent</a>

  <div class="product" style="left:181px">
    <div class="product-inner">
      <svg width="50" height="46" viewBox="0 0 50 46"><path d="M25 2L2 22h6v22h12V30h10v14h12V22h6z" fill="#fff"/></svg>
      Homeowners
    </div>
  </div>
  <div class="product" style="left:400px">
    <div class="product-inner">
      <svg width="46" height="46" viewBox="0 0 48 48" fill="#fff"><rect x="4" y="44" width="40" height="4"/><path d="M8 6h10V0h12v6h10v38H8z"/><g fill="#1a4fa3"><rect x="12" y="10" width="5" height="5"/><rect x="21" y="10" width="5" height="5"/><rect x="30" y="10" width="5" height="5"/><rect x="12" y="19" width="5" height="5"/><rect x="21" y="19" width="5" height="5"/><rect x="30" y="19" width="5" height="5"/><rect x="12" y="28" width="5" height="5"/><rect x="21" y="28" width="5" height="5"/><rect x="30" y="28" width="5" height="5"/><rect x="21" y="37" width="6" height="7"/></g></svg>
      Renters/Condo
    </div>
  </div>
  <div class="product" style="left:620px">
    <div class="product-inner">
      <svg width="64" height="46" viewBox="0 0 64 46"><path d="M24 2L2 22h6v22h32V22h6z" fill="#fff"/><g fill="#1a4fa3"><rect x="13" y="26" width="6" height="6"/><rect x="21" y="26" width="6" height="6"/><rect x="13" y="34" width="6" height="6"/><rect x="21" y="34" width="6" height="6"/></g><path d="M52 10c4 8 10 14 10 24a10 10 0 0 1-20 0c0-5 3-8 4-12 2 3 3 5 3 7 2-5 4-10 3-19z" fill="#fff"/></svg>
      Dwelling Fire
    </div>
  </div>
  <div class="product" style="left:839px">
    <div class="product-inner">
      <svg width="46" height="46" viewBox="0 0 48 50"><path d="M24 2a12 12 0 0 0-12 12c0 9 12 22 12 22s12-13 12-22A12 12 0 0 0 24 2z" fill="#fff"/><circle cx="24" cy="14" r="5" fill="#1a4fa3"/><path d="M10 34h6M32 34h6M10 34L3 48h42l-7-14" stroke="#fff" stroke-width="3" fill="none"/></svg>
      Agent Locator<br>Tool
    </div>
  </div>
</section>

<footer class="footer">
  <div class="col" style="left:172px">
    <h3>Contact Info</h3>
    <div class="phone">1800 555 0142</div>
    <div class="email">info@hearthlineinsurance.co</div>
    <div class="social"><span></span><span></span><span></span><span></span></div>
  </div>
  <div class="col" style="left:392px">
    <h3>Our Company</h3>
    <ul><li>Home</li><li>Insurance</li><li>About Us</li><li>Claims</li><li>Agents</li></ul>
  </div>
  <div class="col" style="left:537px">
    <h3>Login to Your Account</h3>
    <ul><li>Agents Login</li><li>Clients login</li></ul>
  </div>
  <a class="btn btn-footer"><svg width="18" height="18" viewBox="0 0 18 18" fill="none" stroke="#fff" stroke-width="1.6"><circle cx="8" cy="8" r="6.5"/><circle cx="8" cy="6.5" r="2"/><path d="M4.5 11.5c1-2 6-2 7 0M12.7 12.7L17 17"/></svg>Find an Agent</a>
  <div class="col" style="left:734px">
    <h3>Customer Support</h3>
    <ul><li>FAQs</li><li>Resources</li><li>Report a Claim</li><li>Find an Agent</li></ul>
  </div>
  <div class="col" style="left:903px">
    <h3>Connect With Us</h3>
    <ul><li>Support</li><li>Careers</li></ul>
  </div>
  <div class="legal">
    Copyright ©2018 Hearthline Insurance. All Rights Reserved<br>
    Terms of Use &nbsp;-&nbsp; Privacy Policy &nbsp;-&nbsp; Sitemap
  </div>
</footer>
</body>
</html>
```